Hi,

Here are some thoughts on the book cover for The BRIGHT Vitality Map: A Restorative Wellness Path for Active Mothers and their Households.

To simplify this project I've uploaded some images (all images are of a vortex or swirl) that I would like to see the book cover design created with. I've also uploaded a set of "elements" that I would like to see incorporated into the vortex.

My vision is to have you infuse the smaller "elements" into the vortex so they look like they are caught in the vortex or swirling in the vortex.

I have upload an amateur example which I did but it shows the smaller elements dropped into the larger vortex image.

Please don't hesitate to write me with any questions you may have.

Thank you,

Gareth

Please.

Target Market(s)

Busy Women, both stay at home and career women

Industry/Entity Type

Health

Font styles to use
Serif
Sans Serif

Requirements
Must have
• vortex or swirl with circular elements infused

```html
<!DOCTYPE html>
<html lang="en">
<head>
<meta charset="utf-8">
<title>The BRIGHT Vitality Map — Book Cover</title>
<link rel="stylesheet" href="https://fonts.googleapis.com/css2?family=Cinzel:wght@400;600;700&family=Raleway:wght@400&display=swap">
<style>
  :root {
    --peach-light: #fdeee3;
    --peach-mid: #fad6c2;
    --peach-edge: #f6c3a8;
    --title-purple: #8e2a8c;
    --title-blue: #3a5ea8;
    --subtitle-ink: #3b2a2a;
    --band-purple: #a23d95;
    --band-line: #47b8c4;
    --ribbon-light: #c9e36a;
    --ribbon-deep: #7fb825;
    --author-ink: #ffffff;
  }
  html, body {
    margin: 0;
    padding: 0;
    width: 800px;
    height: 1200px;
    overflow: hidden;
    background: #ffffff;
  }
  .cover {
    position: relative;
    width: 800px;
    height: 1200px;
    overflow: hidden;
    background: radial-gradient(ellipse 75% 55% at 50% 48%, var(--peach-light) 0%, var(--peach-mid) 60%, var(--peach-edge) 100%);
  }
  .cover__ribbon {
    position: absolute;
    left: 180px;
    top: 50px;
    width: 300px;
    height: 560px;
    border-radius: 45% 45% 40% 40%;
    background: radial-gradient(ellipse at 50% 40%, var(--ribbon-light) 0%, var(--ribbon-deep) 45%, rgba(127,184,37,0) 72%);
  }
  .cover__title {
    position: absolute;
    left: 0;
    right: 0;
    top: 628px;
    margin: 0;
    text-align: center;
    font-family: "Cinzel", serif;
    font-weight: 600;
    line-height: 1;
  }
  .cover__title-top {
    display: block;
    color: var(--title-purple);
    font-size: 90px;
    letter-spacing: 1px;
  }
  .cover__title-main {
    display: block;
    margin-top: 22px;
    color: var(--title-blue);
    font-size: 88px;
    letter-spacing: 0;
  }
  .cover__subtitle {
    position: absolute;
    left: 60px;
    right: 60px;
    top: 852px;
    margin: 0;
    text-align: center;
    font-family: "Cinzel", serif;
    font-weight: 400;
    font-size: 40px;
    line-height: 50px;
    color: var(--subtitle-ink);
  }
  .cover__band {
    position: absolute;
    left: 0;
    top: 960px;
    width: 800px;
    height: 240px;
  }
  .cover__author {
    position: absolute;
    left: 0;
    right: 0;
    top: 1078px;
    margin: 0;
    text-align: center;
    font-family: "Raleway", sans-serif;
    font-weight: 400;
    font-size: 56px;
    letter-spacing: 18px;
    padding-left: 18px;
    color: var(--author-ink);
  }
</style>
</head>
<body>
  <main class="cover">
    <div class="cover__ribbon" role="img" aria-label="Green ribbon spiral twisting upward"></div>

    <h1 class="cover__title">
      <span class="cover__title-top">The BRIGHT</span>
      <span class="cover__title-main">Vitality Map</span>
    </h1>

    <p class="cover__subtitle">A Restorative Wellness Path for Active Mothers and their Households</p>

    <svg class="cover__band" viewBox="0 0 800 240" aria-hidden="true">
      <path d="M0 62 Q400 22 800 62 L800 240 L0 240 Z" fill="var(--band-purple)"/>
      <path d="M0 60 Q400 20 800 60" fill="none" stroke="var(--band-line)" stroke-width="4"/>
    </svg>

    <p class="cover__author">GARETH</p>
  </main>
</body>
</html>
```